wealth management firm, professional group, new model

we have a logo that works but we need a card, white background using our colors...clean look

our tag line if can be used in

The Bridge From Client to Owner

```html
<!DOCTYPE html>
<html lang="en">
<head>
<meta charset="utf-8">
<title>Halvern Wealth Partners – Business Card</title>
<link href="https://fonts.googleapis.com/css2?family=Jost:wght@400;500;600&display=swap" rel="stylesheet">
<style>
  :root {
    --backdrop: #d3d3d3;
    --card: #ffffff;
    --navy: #17264a;
    --grey: #9a9a9a;
  }
  * { margin: 0; padding: 0; box-sizing: border-box; }
  html, body {
    width: 1200px;
    height: 1000px;
    overflow: hidden;
    background: var(--backdrop);
    font-family: "Jost", "Helvetica Neue", Arial, sans-serif;
  }
  .canvas { position: relative; width: 1200px; height: 1000px; }
  .card {
    position: absolute;
    top: 257px;
    width: 455px;
    height: 488px;
    background: var(--card);
    text-align: center;
  }
  .card--front { left: 125px; }
  .card--back { left: 658px; }

  .brand-name {
    position: absolute;
    left: 0; right: 0;
    color: var(--navy);
    font-weight: 400;
    text-transform: uppercase;
    line-height: 1;
  }
  .card--front .brand-name { top: 228px; }
  .brand-name__main { display: block; font-size: 50px; letter-spacing: 0.32em; padding-left: 0.32em; }
  .brand-name__sub { display: block; font-size: 21px; letter-spacing: 0.12em; margin-top: 28px; }

  .card--back .brand-name { top: 122px; color: var(--grey); }
  .card--back .brand-name__main { font-size: 30px; letter-spacing: 0.3em; padding-left: 0.3em; }
  .card--back .brand-name__sub { font-size: 13px; letter-spacing: 0.1em; margin-top: 18px; }

  .person { position: absolute; top: 232px; left: 0; right: 0; color: var(--navy); }
  .person__name { font-size: 18px; font-weight: 600; letter-spacing: 0.16em; }
  .person__title { font-size: 11px; letter-spacing: 0.14em; margin-top: 8px; }

  .contact-icons {
    position: absolute; top: 298px; left: 0; right: 0;
    display: flex; justify-content: center; gap: 22px;
  }
  .contact-icons svg { width: 26px; height: 26px; stroke: var(--navy); fill: none; stroke-width: 1.2; }

  .contact-list {
    position: absolute; top: 334px; left: 0; right: 0;
    list-style: none; color: var(--navy);
    font-size: 21px; line-height: 29.5px;
  }
</style>
</head>
<body>
<main class="canvas">
  <section class="card card--front" aria-label="Card front">
    <h1 class="brand-name">
      <span class="brand-name__main">Halvern</span>
      <span class="brand-name__sub">Wealth Partners</span>
    </h1>
  </section>

  <section class="card card--back" aria-label="Card back">
    <p class="brand-name">
      <span class="brand-name__main">Halvern</span>
      <span class="brand-name__sub">Wealth Partners</span>
    </p>
    <div class="person">
      <p class="person__name">NAME SURNAME</p>
      <p class="person__title">TITLE</p>
    </div>
    <div class="contact-icons" aria-hidden="true">
      <svg viewBox="0 0 26 26"><path d="M7 3 L10.5 8.5 L8.5 11 C10 14.5 12 16.5 15 18 L17.5 16 L23 19.5 L21 23 C12 23 3 14 3.5 5 Z"/></svg>
      <svg viewBox="0 0 26 26"><rect x="2" y="6" width="22" height="14"/><path d="M2 6 L13 15 L24 6 M2 20 L10 12.5 M24 20 L16 12.5"/></svg>
      <svg viewBox="0 0 26 26"><circle cx="13" cy="13" r="11"/><ellipse cx="13" cy="13" rx="5" ry="11"/><path d="M13 2 V24 M2 13 H24 M4 7.5 H22 M4 18.5 H22"/></svg>
    </div>
    <ul class="contact-list">
      <li>123 456 7890</li>
      <li>name@website.com</li>
      <li>website.com</li>
    </ul>
  </section>
</main>
</body>
</html>
```